Business Card Design

We are a law firm which provides services to creditors.....we do collection litigation. I am wide open on suggestions. I was thinking of a square card? Alternatively, a vertically oriented standard card or a folded card.....something unique. I would like to use my firm logo and beyond that, I am open for any and all suggestions. I'm uncertain if the complete log is uploaded? If not, please let me email it to you.

Industry/Entity Type

Law Firm

Contact Information for Business Card

Hart, Crane & Dobbs, P.C.
Tom Dobbs, Lawyer
4387 N Larkspur Ave
Oklahoma City, OK 73924
tdobbs@HcdCounsel.com
www.HcdCounsel.com
mobile: 405-382-7914

```html
<!DOCTYPE html>
<html lang="en">
<head>
<meta charset="utf-8">
<title>Hart, Crane &amp; Dobbs, P.C. — Business Card</title>
<link rel="stylesheet" href="https://fonts.googleapis.com/css2?family=Arimo:wght@400;700&display=swap">
<style>
  :root {
    --bg: #e8e5e0;
    --card: #ffffff;
    --green: #17864a;
    --green-dark: #0f6b39;
    --gold: #c9a43a;
    --ink: #4a4a4a;
    --ink-soft: #5c5c5c;
    --pattern-a: #f4f4f3;
    --pattern-b: #e6e6e4;
  }
  * { box-sizing: border-box; margin: 0; padding: 0; }
  html, body { width: 1200px; height: 885px; overflow: hidden; }
  body { background: var(--bg); font-family: "Arimo", Arial, sans-serif; position: relative; }

  .card {
    position: absolute; left: 260px; width: 680px; height: 389px;
    background: var(--card); overflow: hidden;
    box-shadow: 0 6px 18px rgba(0,0,0,.18);
  }
  .card--front { top: 33px; }
  .card--back { top: 462px; }

  .front__panel { position: absolute; inset: 0; width: 240px; height: 389px; }

  .brand {
    position: absolute; display: flex; align-items: center; gap: 10px;
    color: #ffffff; font-weight: 700; font-size: 17px; line-height: 1.2;
  }
  .brand__dot { width: 20px; height: 20px; border-radius: 50%; background: var(--gold); flex: none; }
  .front .brand { left: 26px; top: 160px; width: 160px; }

  .front__text { position: absolute; left: 262px; top: 34px; right: 30px; }
  .person__name { color: var(--green); font-size: 38px; font-weight: 700; line-height: 1; }
  .person__role { color: var(--ink); font-size: 23px; font-weight: 700; margin-top: 6px; }
  .address { color: var(--ink-soft); font-size: 15px; line-height: 1.45; margin-top: 16px; }
  .firm { color: var(--ink); font-size: 33px; font-weight: 700; margin-top: 16px; white-space: nowrap; }
  .contacts { list-style: none; margin-top: 16px; }
  .contacts li { display: flex; align-items: center; gap: 8px; color: var(--ink); font-size: 16px; height: 23px; }
  .contacts svg { width: 16px; height: 16px; flex: none; }

  .back__pattern { position: absolute; inset: 0; width: 680px; height: 389px; }
  .back__url {
    position: absolute; left: 0; right: 0; top: 70px; text-align: center;
    color: var(--ink); font-size: 30px;
  }
  .back .brand {
    left: 50%; top: 200px; transform: translateX(-50%);
    color: var(--green); font-size: 24px; white-space: nowrap;
  }
</style>
</head>
<body>

<section class="card card--front front" aria-label="Business card front">
  <svg class="front__panel" viewBox="0 0 240 389" aria-hidden="true">
    <polygon points="0,0 150,0 222,194 150,389 0,389" fill="var(--green)"/>
    <polyline points="150,0 222,194 150,389" fill="none" stroke="var(--gold)" stroke-width="5"/>
  </svg>
  <div class="brand">
    <span class="brand__dot"></span>
    <span class="brand__name">Hart, Crane &amp; Dobbs</span>
  </div>

  <div class="front__text">
    <h1 class="person__name">Tom Dobbs</h1>
    <p class="person__role">Lawyer</p>
    <p class="address">4387 N Larkspur Ave<br>Oklahoma City, OK 73924</p>
    <p class="firm">Hart, Crane &amp; Dobbs, P.C.</p>
    <ul class="contacts">
      <li>
        <svg viewBox="0 0 16 16" aria-hidden="true"><rect width="16" height="16" rx="2" fill="var(--green)"/><rect x="5" y="3" width="6" height="10" rx="1" fill="none" stroke="#fff" stroke-width="1.4"/><circle cx="8" cy="11" r=".8" fill="#fff"/></svg>
        405-382-7914
      </li>
      <li>
        <svg viewBox="0 0 16 16" aria-hidden="true"><rect width="16" height="16" rx="2" fill="var(--green)"/><rect x="3" y="4.5" width="10" height="7" fill="none" stroke="#fff" stroke-width="1.3"/><polyline points="3,4.5 8,9 13,4.5" fill="none" stroke="#fff" stroke-width="1.3"/></svg>
        tdobbs@HcdCounsel.com
      </li>
      <li>
        <svg viewBox="0 0 16 16" aria-hidden="true"><rect width="16" height="16" rx="2" fill="var(--green)"/><circle cx="8" cy="8" r="5" fill="none" stroke="#fff" stroke-width="1.2"/><ellipse cx="8" cy="8" rx="2.2" ry="5" fill="none" stroke="#fff" stroke-width="1"/><line x1="3" y1="8" x2="13" y2="8" stroke="#fff" stroke-width="1"/></svg>
        www.HcdCounsel.com
      </li>
    </ul>
  </div>
</section>

<section class="card card--back back" aria-label="Business card back">
  <svg class="back__pattern" viewBox="0 0 680 389" role="img" aria-label="Faint repeating background pattern">
    <defs>
      <radialGradient id="backTone" cx="50%" cy="50%" r="70%">
        <stop offset="0" stop-color="var(--pattern-a)"/>
        <stop offset="1" stop-color="var(--pattern-b)"/>
      </radialGradient>
    </defs>
    <rect width="680" height="389" fill="url(#backTone)"/>
  </svg>
  <p class="back__url">www.HcdCounsel.com</p>
  <div class="brand">
    <span class="brand__dot"></span>
    <span class="brand__name">Hart, Crane &amp; Dobbs</span>
  </div>
</section>

</body>
</html>
```